I need a complete stationary pack for a real estate office that sells and manages residential proper

We need a stationary design pack for my real estate office called ‘brightkeyhomes’ that is in Queensland Australia. My offices are both in suburban and coastal locations in the south west corner of Queensland at the Coral Bay Shore and Brisbane.
We predominately manage real estate on behalf of owners and sell property in the residential sector.
I have attached a copy of our existing design of my business card and do like the current concept/layout. In saying this you may be able to use this existing theme across to the other items required or see opportunity on how to improve what I have already.
I would like to see concepts for the following products:
- Letterhead
- Fax header
- Business cards
- Email signature
- With complements slips and
- Envelopes
I have attached our current logo that was designed by Artfolder and the font is Prelo.

I am looking for a contemporary design that is professional and reflects trust and professionalism. I am currently using the logo with a black background on some material as per the following link

http://www.plotlisting.com.au/property/for-sale/house/qld/merridale/?adid=4827305118&sp=7

I have posted another job 517362 for signage and the company car signage done too if you are interested.

Please do not hesitate to contact me should you have any questions. Thank you.

Target Market(s)

Western speaking people aged from 25 to 60 from modest backgrounds to well off individuals

Industry/Entity Type

Real Estate

Requirements
Must have
• Professional in appearance, show a mature and trustworthy image
Should not have
• As there is good colour with the logo, i am do not want over the top designs or colours

```html
<!DOCTYPE html>
<html lang="en">
<head>
<meta charset="utf-8">
<title>brightkeyhomes business card</title>
<link href="https://fonts.googleapis.com/css2?family=Open+Sans:wght@400;600;700&display=swap" rel="stylesheet">
<style>
  :root {
    --backdrop: #ece8e2;
    --card-black: #111111;
    --card-black-sheen: #2a2a2a;
    --card-white: #ffffff;
    --ink: #555a60;
    --ink-dark: #2f3338;
    --name-red: #d6262d;
    --role-green: #2fa84f;
    --rule-green: #3aaa47;
    --link-blue: #2a7fc1;
    --photo-sky: #6f9ccc;
    --photo-suit: #2c3440;
    --on-dark: #f2f2f2;
  }
  * { box-sizing: border-box; margin: 0; padding: 0; }
  html, body {
    width: 1200px; height: 1024px; overflow: hidden;
    background: var(--backdrop);
    font-family: "Open Sans", Arial, sans-serif;
  }
  .stage { position: relative; width: 1200px; height: 1024px; }

  .card {
    position: absolute;
    width: 560px; height: 320px;
    border-radius: 4px;
    box-shadow: 0 14px 30px rgba(0,0,0,.22);
    overflow: hidden;
  }

  /* Front */
  .card-front {
    left: 90px; top: 110px;
    background: linear-gradient(135deg, var(--card-black-sheen) 0%, var(--card-black) 45%, var(--card-black) 100%);
  }
  .front-brand {
    position: absolute; left: 40px; bottom: 74px;
    color: var(--on-dark); font-weight: 600; font-size: 46px; letter-spacing: -0.5px;
  }
  .front-url {
    position: absolute; left: 42px; bottom: 46px;
    color: var(--on-dark); font-weight: 600; font-size: 17px;
  }

  /* Back */
  .card-back {
    left: 550px; top: 594px;
    background: var(--card-white);
  }
  .back-brand {
    position: absolute; left: 34px; top: 42px;
    color: var(--ink-dark); font-weight: 600; font-size: 34px; letter-spacing: -0.4px;
  }
  .back-rule {
    position: absolute; left: 34px; right: 34px; top: 122px;
    height: 2px; background: var(--rule-green);
  }
  .portrait {
    position: absolute; left: 34px; top: 146px;
    width: 112px; height: 128px;
    background: linear-gradient(180deg, var(--photo-sky) 0%, var(--photo-sky) 55%, var(--photo-suit) 100%);
  }
  .details {
    position: absolute; left: 168px; top: 142px;
    font-size: 13.5px; line-height: 19px; color: var(--ink);
  }
  .details .name { color: var(--name-red); font-weight: 700; font-size: 17px; line-height: 22px; }
  .details .role { color: var(--role-green); margin-bottom: 2px; }
  .details .address { margin-bottom: 6px; }
  .details .label { color: var(--name-red); font-weight: 600; margin-right: 4px; }
  .details .web { color: var(--link-blue); }
</style>
</head>
<body>
<main class="stage">
  <section class="card card-front" aria-label="Business card front">
    <div class="front-brand">brightkeyhomes</div>
    <div class="front-url">www.brightkeyhomes.com.au</div>
  </section>

  <section class="card card-back" aria-label="Business card back">
    <div class="back-brand">brightkeyhomes</div>
    <div class="back-rule"></div>
    <div class="portrait" role="img" aria-label="Portrait photo of the principal"></div>
    <div class="details">
      <div class="name">Darren Holcott</div>
      <div class="role">Principal</div>
      <div class="address">shop 4, 212 harbour rd,<br>merridale qld 4581</div>
      <div><span class="label">M:</span>0412 558 907</div>
      <div><span class="label">P:</span>07 5491 2064</div>
      <div><span class="label">E:</span>darren@brightkeyhomes.com.au</div>
      <div class="web">www.brightkeyhomes.com.au</div>
    </div>
  </section>
</main>
</body>
</html>
```